Business Card for Coastal Tundrabridge Advisory

We need a business card for Coastal Tundrabridge Advisory. The company website address is provided below. The company logo is attached. We provide specialized permafrost services to the mining, transportation, and oil & gas industries. The card should be prepared for:
Matthias Korhonen, PhD.
Coastal Tundrabridge Advisory
PO Box 418259
Quillwater, Alaska 99642
Direct: +1-907-555-0143
Email: mkorhonen@tundrabridgeadvisory.example
Website: www.coastaltundrabridgeadvisory.example

```html
<!DOCTYPE html>
<html lang="en">
<head>
<meta charset="utf-8">
<title>Coastal Tundrabridge Advisory – Business Card</title>
<link rel="stylesheet" href="https://fonts.googleapis.com/css2?family=Arimo:wght@400;700&display=swap">
<style>
  :root {
    --bg: #d9dadc;
    --ink-dark: #0f171f;
    --paper: #ffffff;
    --text-light: #ffffff;
    --divider-a: #9ea2a7;
    --divider-b: #3a4047;
    --brand-grey: #8b9198;
    --shadow: rgba(0, 0, 0, 0.25);
  }
  * { box-sizing: border-box; margin: 0; padding: 0; }
  html, body {
    width: 1200px; height: 800px; overflow: hidden;
    background: var(--bg);
    font-family: "Arimo", Arial, sans-serif;
  }
  .stage {
    width: 1200px; height: 800px;
    display: flex; align-items: center; justify-content: center; gap: 40px;
  }
  .card {
    width: 540px; height: 309px; border-radius: 18px; overflow: hidden;
    box-shadow: 0 10px 24px var(--shadow);
    position: relative;
  }
  /* Front card */
  .card-front { display: flex; }
  .brand-panel {
    width: 210px; background: var(--paper);
    display: flex; align-items: center; justify-content: center;
    padding: 0 18px;
  }
  .brand-name {
    color: var(--ink-dark); font-weight: 700; font-size: 15px;
    letter-spacing: 0.12em; text-transform: uppercase;
    text-align: center; line-height: 1.45;
  }
  .panel-divider {
    width: 6px;
    background: linear-gradient(90deg, var(--divider-a), var(--divider-b));
  }
  .info-panel {
    flex: 1; background: var(--ink-dark); color: var(--text-light);
    padding: 24px 18px 22px 12px;
    display: flex; flex-direction: column; align-items: flex-end; text-align: right;
  }
  .person-name { font-size: 21px; font-weight: 700; line-height: 1.1; }
  .person-title { font-size: 13px; margin-top: 3px; }
  .address { font-size: 12.5px; line-height: 1.5; margin-top: 36px; }
  .contacts { margin-top: 8px; font-size: 12px; line-height: 1.6; }
  .contact-line { display: flex; justify-content: flex-end; align-items: center; gap: 6px; }
  .contact-line svg { width: 11px; height: 11px; flex: none; fill: var(--text-light); }
  .web-block { margin-top: auto; font-size: 12px; line-height: 1.6; }
  /* Back card */
  .card-back {
    background: var(--ink-dark);
    display: flex; align-items: center; justify-content: center;
  }
  .brand-name-large {
    color: var(--brand-grey); font-weight: 700; font-size: 30px;
    letter-spacing: 0.12em; text-transform: uppercase;
    text-align: center; line-height: 1.35;
  }
</style>
</head>
<body>
<main class="stage">
  <section class="card card-front" aria-label="Business card front">
    <div class="brand-panel">
      <p class="brand-name">Coastal Tundrabridge Advisory</p>
    </div>
    <div class="panel-divider"></div>
    <div class="info-panel">
      <h1 class="person-name">Matthias Korhonen, PhD.</h1>
      <p class="person-title">President</p>
      <p class="address">PO Box 418259<br>Quillwater, Alaska 99642</p>
      <div class="contacts">
        <p class="contact-line">+1-907-555-0143
          <svg viewBox="0 0 24 24" aria-hidden="true"><path d="M6.6 10.8a15.1 15.1 0 0 0 6.6 6.6l2.2-2.2a1 1 0 0 1 1-.25 11.4 11.4 0 0 0 3.6.57 1 1 0 0 1 1 1V20a1 1 0 0 1-1 1A17 17 0 0 1 3 4a1 1 0 0 1 1-1h3.5a1 1 0 0 1 1 1c0 1.25.2 2.45.57 3.57a1 1 0 0 1-.25 1z"/></svg>
        </p>
      </div>
      <div class="web-block">
        <p class="contact-line">mkorhonen@tundrabridgeadvisory.example
          <svg viewBox="0 0 24 24" aria-hidden="true"><path d="M2 5h20v14H2z M4 7v.5l8 5 8-5V7l-8 5z" fill-rule="evenodd"/></svg>
        </p>
        <p class="contact-line">www.coastaltundrabridgeadvisory.example
          <svg viewBox="0 0 24 24" aria-hidden="true"><circle cx="12" cy="12" r="10"/></svg>
        </p>
      </div>
    </div>
  </section>

  <section class="card card-back" aria-label="Business card back">
    <p class="brand-name-large">Coastal<br>Tundrabridge<br>Advisory</p>
  </section>
</main>
</body>
</html>
```